The Aldermoor- outdoor banner

This should be a horizontal banner. It should have the logos attached incorporated and the following details
Coming Spring 2025: The Aldermoor - Exclusive Luxury Condos
Listed by Marisol Quennell | Fairlight Realty
Construction by Stonegate Build Group
Unveil the height of luxury living with The Aldermoor, a new condo building in East Boston, set for completion in Spring 2025. Experience a standard of elegance and sophistication like never before.
For more information and inquiries, please contact:
Marisol Quennell
Phone: (617) 430-9162
Email: marisol@fairlightprops.com
The banner should be very classy incorporting gold and navy very classic fonts. The Aldermoor should look very classy and exclusive. The stonegate build group logo should be smaller. It should not include their phone number and instagram handle only the name of the company. Herringbone pattern in the background would be great. This is going outside the building to advertise pre construction units

```html
<!DOCTYPE html>
<html lang="en">
<head>
<meta charset="utf-8">
<title>The Aldermoor – Outdoor Banner</title>
<link rel="stylesheet" href="https://fonts.googleapis.com/css2?family=Bodoni+Moda:wght@500;600&family=Great+Vibes&family=Mulish:wght@600;700&display=swap">
<style>
  :root {
    --navy: #1f3158;
    --navy-deep: #17264a;
    --navy-light: #2a4273;
    --gold: #e2b15e;
    --white: #ffffff;
    --page: #ffffff;
  }
  * { margin: 0; padding: 0; box-sizing: border-box; }
  html, body { width: 943px; height: 1200px; overflow: hidden; background: var(--page); }
  .canvas { position: relative; width: 943px; height: 1200px; }
  .banner {
    position: absolute; left: 32px; top: 380px; width: 878px; height: 440px;
    overflow: hidden; color: var(--white); font-family: "Mulish", sans-serif; font-weight: 600;
  }
  .banner-backdrop {
    position: absolute; inset: 0;
    background:
      radial-gradient(ellipse at 20% 15%, rgba(60, 88, 140, 0.45) 0%, rgba(60, 88, 140, 0) 55%),
      radial-gradient(ellipse at 90% 20%, rgba(52, 80, 132, 0.4) 0%, rgba(52, 80, 132, 0) 50%),
      linear-gradient(135deg, var(--navy-light) 0%, var(--navy) 45%, var(--navy-deep) 100%);
  }
  .listing-column {
    position: absolute; left: 0; top: 0; width: 316px; height: 100%; text-align: center;
  }
  .listed-by { position: absolute; top: 38px; width: 100%; font-size: 15.5px; white-space: nowrap; }
  .realty-mark {
    position: absolute; top: 74px; left: 50%; transform: translateX(-50%);
    width: 88px; height: 88px; border: 3px solid var(--gold); border-radius: 50%;
  }
  .realty-name {
    position: absolute; top: 172px; width: 100%;
    font-family: "Bodoni Moda", serif; font-weight: 500; font-size: 25px;
    letter-spacing: 1.5px; color: var(--gold); text-transform: uppercase; white-space: nowrap;
  }
  .construction-label {
    position: absolute; top: 232px; left: 50%; transform: translateX(-50%);
    width: 141px; height: 21px; border: 1px solid var(--gold); border-radius: 3px;
    font-size: 14px; line-height: 19px; white-space: nowrap;
  }
  .builder-name {
    position: absolute; top: 292px; width: 100%; font-size: 13px; font-weight: 700;
    letter-spacing: 0.5px; text-transform: uppercase; white-space: nowrap;
  }
  .inquiry-note { position: absolute; top: 345px; width: 100%; font-size: 13px; line-height: 17px; }
  .agent-name { position: absolute; top: 385px; width: 100%; font-size: 20px; color: var(--gold); white-space: nowrap; }

  .project-column { position: absolute; left: 324px; top: 0; width: 540px; height: 100%; }
  .launch-badge {
    position: absolute; left: 0; top: 46px; width: 263px; height: 32px;
    background: var(--gold); color: var(--navy-deep);
    font-size: 20px; font-weight: 700; line-height: 32px; text-align: center; white-space: nowrap;
  }
  .title-article {
    position: absolute; left: 285px; top: 30px; font-family: "Great Vibes", cursive;
    font-size: 58px; color: var(--gold); line-height: 1;
  }
  .project-title {
    position: absolute; left: 4px; top: 80px; font-family: "Bodoni Moda", serif; font-weight: 600;
    font-size: 72px; line-height: 1; letter-spacing: -1px; text-transform: uppercase; white-space: nowrap;
  }
  .project-tagline {
    position: absolute; left: 4px; top: 164px; font-family: "Bodoni Moda", serif; font-weight: 500;
    font-size: 39px; line-height: 1; letter-spacing: -0.5px; white-space: nowrap;
  }
  .title-rule { position: absolute; left: 0; top: 224px; width: 528px; height: 1px; background: var(--gold); }
  .project-description { position: absolute; left: 5px; top: 246px; font-size: 15px; line-height: 21px; white-space: nowrap; }
  .project-description .highlight { color: var(--gold); }
  .contact-list { position: absolute; left: 5px; top: 362px; list-style: none; }
  .contact-item { display: flex; align-items: center; gap: 10px; font-size: 19px; line-height: 26px; white-space: nowrap; }
  .contact-icon { width: 17px; height: 17px; fill: var(--gold); }
</style>
</head>
<body>
<div class="canvas">
  <section class="banner">
    <div class="banner-backdrop" role="img" aria-label="Navy herringbone wood pattern background"></div>

    <div class="listing-column">
      <p class="listed-by">Listed by Marisol Quennell</p>
      <div class="realty-mark"></div>
      <p class="realty-name">Fairlight Realty</p>
      <p class="construction-label">Construction by</p>
      <p class="builder-name">Stonegate Build Group</p>
      <p class="inquiry-note">For more information and inquiries,<br>please contact:</p>
      <p class="agent-name">Marisol Quennell</p>
    </div>

    <div class="project-column">
      <p class="launch-badge">COMING SPRING 2025</p>
      <h1 class="project-title">Aldermoor</h1>
      <span class="title-article">The</span>
      <p class="project-tagline">Exclusive Luxury Condos</p>
      <div class="title-rule"></div>
      <p class="project-description">
        Unveil the height of luxury living with The Aldermoor,<br>
        a new condo building in East Boston, set for completion in Spring 2025.<br>
        <span class="highlight">Experience a standard of elegance and sophistication like never before.</span>
      </p>
      <ul class="contact-list">
        <li class="contact-item">
          <svg class="contact-icon" viewBox="0 0 24 24" aria-hidden="true"><path d="M6.6 10.8a15.1 15.1 0 0 0 6.6 6.6l2.2-2.2c.3-.3.7-.4 1-.2 1.1.4 2.3.6 3.6.6.6 0 1 .4 1 1V20c0 .6-.4 1-1 1A17 17 0 0 1 3 4c0-.6.4-1 1-1h3.5c.6 0 1 .4 1 1 0 1.3.2 2.5.6 3.6.1.3 0 .7-.2 1z"/></svg>
          (617) 430-9162
        </li>
        <li class="contact-item">
          <svg class="contact-icon" viewBox="0 0 24 24" aria-hidden="true"><path d="M2 6.2V19h20V6.2l-10 7.6z M2.8 5 12 12 21.2 5z"/></svg>
          marisol@fairlightprops.com
        </li>
      </ul>
    </div>
  </section>
</div>
</body>
</html>
```